Men's and Boys sports themed barbershop. I was wanting to see what a black card would look like. I think white is too plain, but I am just needing some ideas for a design or background.

Contact Information for Business Card

Ace Trims
4185 E. Harbor Pine Blvd
Fernhaven, Fl 30917
(555) 555-0142
ace_trims@fernmail.example
Denise Walcott (on one side) Curtis Walcott (on opposite side)
Owner
(555) 555-0187 (Denise) (555) 555-0163

```html
<!DOCTYPE html>
<html lang="en">
<head>
<meta charset="utf-8">
<title>Ace Trims — Business Cards</title>
<link rel="stylesheet" href="https://fonts.googleapis.com/css2?family=Crimson+Pro:wght@400;700&display=swap">
<style>
  :root {
    --backdrop: #7d7d7d;
    --card-glow: #3b3b3b;
    --card-edge: #0b0b0b;
    --ink: #f4f4f4;
    --ink-soft: #dcdcdc;
    --icon: #8a8a8a;
    --brand: #f4f4f4;
    --shadow: rgba(0, 0, 0, 0.45);
  }
  * { margin: 0; padding: 0; box-sizing: border-box; }
  html, body { width: 1200px; height: 1000px; overflow: hidden; }
  body {
    position: relative;
    background: var(--backdrop);
    font-family: "Crimson Pro", Georgia, serif;
    color: var(--ink);
  }
  .card {
    position: absolute;
    width: 757px;
    height: 432px;
    background: radial-gradient(ellipse 60% 70% at 48% 52%, var(--card-glow) 0%, #1c1c1c 55%, var(--card-edge) 100%);
    box-shadow: 6px 8px 10px var(--shadow);
  }
  .card--front { left: 52px; top: 47px; }
  .card--back { left: 379px; top: 518px; }

  .brand {
    position: absolute;
    text-align: center;
    color: var(--brand);
  }
  .brand__name {
    display: block;
    font-weight: 700;
    font-size: 80px;
    line-height: 1;
    letter-spacing: 1px;
  }
  .brand__tagline {
    display: block;
    font-weight: 400;
    font-size: 36px;
    letter-spacing: 4px;
    margin-top: 38px;
    color: var(--ink-soft);
  }
  .card--front .brand { left: 50px; top: 50px; width: 480px; }
  .card--back .brand { left: 140px; top: 36px; width: 480px; }

  .contact-name { font-size: 34px; font-weight: 400; line-height: 1; }
  .card--front .contact-name { position: absolute; left: 30px; top: 276px; }

  .contact-list { position: absolute; left: 32px; top: 324px; list-style: none; }
  .contact-list li {
    display: flex; align-items: center; gap: 6px;
    font-size: 20px; line-height: 25px; color: var(--ink-soft);
  }
  .icon {
    width: 26px; height: 20px; flex: none;
    fill: none; stroke: var(--icon); stroke-width: 1.4;
  }

  .person { position: absolute; }
  .person--owner { left: 31px; top: 298px; }
  .person--owner .contact-name { font-size: 52px; }
  .person__role { font-size: 27px; line-height: 1; margin-top: 2px; }
  .person__phone {
    display: flex; align-items: center; gap: 4px;
    font-size: 21px; color: var(--ink-soft); margin-top: 6px;
  }
  .person--staff { right: 28px; top: 336px; text-align: right; }
  .person--staff .contact-name { font-size: 44px; }
  .person--staff .person__phone { justify-content: flex-end; margin-top: 8px; }
</style>
</head>
<body>

<svg width="0" height="0" style="position:absolute" aria-hidden="true">
  <defs>
    <symbol id="icon-phone" viewBox="0 0 26 20">
      <path d="M2 7 Q13 1 24 7 L22 10 L18 8 L18 6 Q13 4.5 8 6 L8 8 L4 10 Z"/>
      <rect x="5" y="10" width="16" height="8" rx="1"/>
      <circle cx="13" cy="14" r="2.4"/>
    </symbol>
    <symbol id="icon-home" viewBox="0 0 26 20">
      <path d="M3 10 L13 2 L23 10"/>
      <rect x="6" y="9" width="14" height="10"/>
      <rect x="11" y="13" width="4" height="6"/>
    </symbol>
    <symbol id="icon-mail" viewBox="0 0 26 20">
      <rect x="3" y="4" width="20" height="13"/>
      <path d="M3 4 L13 12 L23 4"/>
    </symbol>
  </defs>
</svg>

<section class="card card--front">
  <div class="brand">
    <span class="brand__name">Ace Trims</span>
    <span class="brand__tagline">Game Day Fresh!</span>
  </div>
  <h2 class="contact-name">Denise Walcott</h2>
  <ul class="contact-list">
    <li><svg class="icon"><use href="#icon-home"/></svg>4185 E. Harbor Pine Blvd Fernhaven, Fl 30917</li>
    <li><svg class="icon"><use href="#icon-phone"/></svg>(555) 555-0142</li>
    <li><svg class="icon"><use href="#icon-mail"/></svg>ace_trims@fernmail.example</li>
  </ul>
</section>

<section class="card card--back">
  <div class="brand">
    <span class="brand__name">Ace Trims</span>
    <span class="brand__tagline">Game Day Fresh!</span>
  </div>
  <div class="person person--owner">
    <h2 class="contact-name">Curtis Walcott</h2>
    <p class="person__role">(Owner)</p>
    <p class="person__phone"><svg class="icon"><use href="#icon-phone"/></svg>(555) 555-0187</p>
  </div>
  <div class="person person--staff">
    <h2 class="contact-name">Denise Walcott</h2>
    <p class="person__phone"><svg class="icon"><use href="#icon-phone"/></svg>(555) 555-0163</p>
  </div>
</section>

</body>
</html>
```